business card deign

Logo needs the following on it.
1. attached logo
2. Tagline - "Whatever keeps the cooler full and the night rolling...we bring it!"
3. Name- Dalton Pikes, Founder and CPO
4. Address - 412 E. Carver Avenue, Ste 2207, Tampa, FL. 33917
5. Phone - 555.318.4726

```html
<!DOCTYPE html>
<html lang="en">
<head>
<meta charset="UTF-8">
<title>Tundro Business Card</title>
<link href="https://fonts.googleapis.com/css2?family=Roboto:wght@400;700&display=swap" rel="stylesheet">
<style>
  :root {
    --stage: #232323;
    --card: #161616;
    --card-edge: #1c1c1c;
    --ink: #ffffff;
    --ink-soft: #e6e6e6;
    --rule: #bdbdbd;
    --pattern-light: #8a8a8a;
    --pattern-dark: #0d0d0d;
  }
  * { box-sizing: border-box; margin: 0; padding: 0; }
  html, body {
    width: 1200px; height: 780px; overflow: hidden;
    background: var(--stage);
    font-family: "Roboto", Arial, sans-serif;
    color: var(--ink);
  }
  .stage { position: relative; width: 1200px; height: 780px; }
  .card {
    position: absolute;
    width: 560px; height: 320px;
    border-radius: 26px;
    background: var(--card);
    box-shadow: 0 18px 40px rgba(0,0,0,.55);
    overflow: hidden;
  }
  .card--back { left: 70px; top: 60px; }
  .card--front { left: 570px; top: 400px; background: var(--card-edge); }

  .back-pattern {
    position: absolute; inset: 0;
    background: linear-gradient(135deg, var(--pattern-light) 0%, #2a2a2a 35%, var(--pattern-dark) 100%);
    opacity: .55;
  }

  .brand {
    position: absolute; left: 40px; top: 0; bottom: 0; width: 220px;
    display: flex; align-items: center; justify-content: center; gap: 12px;
  }
  .brand__mark { width: 22px; height: 22px; border-radius: 50%; background: var(--ink); }
  .brand__name { font-weight: 700; font-size: 30px; letter-spacing: 8px; }

  .divider {
    position: absolute; left: 270px; top: 60px; width: 1px; height: 150px;
    background: var(--rule);
  }

  .details { position: absolute; left: 300px; top: 62px; }
  .details__name { font-weight: 700; font-size: 26px; line-height: 1.1; }
  .details__title { font-size: 15px; color: var(--ink-soft); margin-top: 4px; }
  .contact { list-style: none; margin-top: 22px; font-size: 12.5px; color: var(--ink-soft); }
  .contact li { display: flex; gap: 8px; align-items: flex-start; margin-bottom: 4px; line-height: 1.35; }
  .contact svg { flex: none; margin-top: 1px; }

  .tagline {
    position: absolute; left: 0; right: 0; bottom: 30px;
    text-align: center; font-size: 13px; color: var(--ink-soft); padding-left: 120px;
  }
</style>
</head>
<body>
<main class="stage">
  <section class="card card--back">
    <div class="back-pattern" role="img" aria-label="Repeating brand symbol pattern in silver fading to black"></div>
  </section>

  <section class="card card--front">
    <div class="brand">
      <span class="brand__mark"></span>
      <span class="brand__name">TUNDRO</span>
    </div>
    <div class="divider"></div>
    <div class="details">
      <h1 class="details__name">Dalton Pikes</h1>
      <p class="details__title">Founder and CPO</p>
      <ul class="contact">
        <li>
          <svg width="12" height="12" viewBox="0 0 24 24" fill="none" stroke="#fff" stroke-width="2.2"><path d="M5 3h4l2 5-2.5 1.5a11 11 0 0 0 6 6L16 13l5 2v4a2 2 0 0 1-2 2A17 17 0 0 1 3 5a2 2 0 0 1 2-2z"/></svg>
          <span>555.318.4726</span>
        </li>
        <li>
          <svg width="12" height="14" viewBox="0 0 24 28" fill="none" stroke="#fff" stroke-width="2.2"><path d="M12 26s8-8 8-15a8 8 0 0 0-16 0c0 7 8 15 8 15z"/><circle cx="12" cy="11" r="3"/></svg>
          <span>412 E. Carver Avenue,<br>Ste 2207, Tampa, FL. 33917</span>
        </li>
      </ul>
    </div>
    <p class="tagline">Whatever keeps the cooler full and the night rolling...we bring it!</p>
  </section>
</main>
</body>
</html>
```